Tolvane Inc., a third party debt collection agency needs a Website

Tolvane needs a very basic website (3 basic pages) so that consumers can download forms, potential employees can get required EEO language and see potential jobs, and to show that they are a consumer friendly organization.

I've attached a list of requirements and wishes titled "Tolvane Website Specifications"

Target Market(s)

Consumers that need to repay their government loans; Tolvane will walk through the process to assist them.

Industry/Entity Type

Financial Service

Coding

Coded - Design and coding required

Number of Pages Required

1 page

Font styles to use
Sans Serif

Colors
0355a3

Requirements
Must have
• Tolvane Logo
• See document "Tolvane Website Specifications" for all requirements

```html
<!DOCTYPE html>
<html lang="en">
<head>
<meta charset="utf-8">
<title>Tolvane Inc.</title>
<link href="https://fonts.googleapis.com/css2?family=Open+Sans:wght@400;600;700&family=Roboto+Condensed:wght@400;700&family=Roboto:wght@400&display=swap" rel="stylesheet">
<style>
:root{
  --navy:#262a6e;
  --red:#8b1a1a;
  --text:#666;
  --grey-band:#f4f4f4;
  --white:#fff;
  --line:#d8d8d8;
}
*{margin:0;padding:0;box-sizing:border-box}
html,body{width:720px;height:1200px;overflow:hidden;background:var(--white)}
body{font-family:"Open Sans",sans-serif;color:var(--text);position:relative}

.site-header{position:absolute;top:0;left:0;width:720px;height:72px}
.brand{position:absolute;left:46px;top:20px;display:flex;align-items:center;gap:8px}
.brand-mark{width:22px;height:22px;border-radius:50%;background:var(--navy)}
.brand-name{font-family:"Roboto Condensed",sans-serif;font-weight:700;font-size:22px;color:var(--red)}
.hotline{position:absolute;right:47px;top:10px;display:flex;align-items:center;gap:6px;font-family:"Roboto Condensed",sans-serif}
.hotline-label{font-size:17px;color:var(--navy)}
.hotline-number{font-size:19px;font-weight:700;color:var(--red)}
.main-nav{position:absolute;right:46px;top:41px;display:flex;gap:20px;font-family:"Roboto",sans-serif;font-size:12px;color:#888}
.main-nav .active{color:var(--navy)}

.hero{position:absolute;top:72px;left:0;width:720px;height:344px}
.hero-photo{position:absolute;inset:0;background:linear-gradient(90deg,#f3f4f6 0%,#eceef1 35%,#d9d5d3 60%,#e8e6e4 80%,#f1f1f1 100%)}
.hero-title{position:absolute;left:48px;top:98px;font-family:"Roboto Condensed",sans-serif;font-weight:400;font-size:28px;line-height:37.5px;color:var(--navy)}
.hero-button{position:absolute;left:46px;top:222px;width:238px;height:38px;background:var(--red);color:var(--white);border-radius:2px;font-family:"Roboto Condensed",sans-serif;font-size:15px;display:flex;align-items:center;justify-content:center}

.welcome{position:absolute;top:416px;left:0;width:720px;height:159px;text-align:center}
.section-title{font-family:"Roboto Condensed",sans-serif;font-weight:400;font-size:27px;color:var(--navy)}
.section-title em{font-style:normal;color:var(--red)}
.welcome .section-title{margin-top:30px}
.welcome p{width:560px;margin:10px auto 0;font-size:9.6px;line-height:15px}

.credentials{position:absolute;top:575px;left:0;width:720px;height:194px;background:var(--grey-band)}
.credentials .divider{position:absolute;left:360px;top:27px;width:1px;height:134px;background:var(--line)}
.credential{position:absolute;top:40px;display:flex}
.credential-badge{height:110px;flex:none;display:flex;align-items:flex-start;justify-content:center}
.credential-badge span{display:block;width:76px;height:76px;background:#4a8ec6;border-radius:4px;margin-top:2px}
.credential-badge.round span{background:#1f6a9e;border-radius:50%}
.credential-text{width:185px}
.credential h3{font-weight:400;font-size:14px;line-height:19px;color:var(--navy);margin-top:-2px}
.credential p{font-size:9.6px;line-height:15px;margin-top:4px}
.credential.left{left:44px;gap:24px}
.credential.left .credential-badge{width:92px}
.credential.right{left:386px;gap:20px}
.credential.right .credential-badge{width:80px}
.credential.right .credential-text{width:182px}

.testimonials{position:absolute;top:769px;left:0;width:720px;height:201px;text-align:center}
.testimonials .section-title{margin-top:28px}
.quote-icon{margin:4px auto 0;display:block}
.testimonials blockquote{width:510px;margin:8px auto 0;font-size:9.6px;line-height:15px}
.client-name{margin-top:14px;font-size:9.6px;color:var(--navy)}
.slide-arrow{position:absolute;top:88px;width:37px;height:37px;border:1px solid #ccc;border-radius:50%;background:var(--white);display:flex;align-items:center;justify-content:center}
.slide-arrow.prev{left:56px}
.slide-arrow.next{left:636px}

.news{position:absolute;top:970px;left:0;width:720px;height:156px;background:var(--grey-band)}
.news .section-title{text-align:center;margin-top:30px}
.news-list{position:absolute;top:72px;left:0;width:720px}
.news-item{position:absolute;display:flex;gap:6px}
.news-date{width:43px;height:50px;background:var(--white);text-align:center;flex:none}
.news-date strong{display:block;font-family:"Roboto Condensed",sans-serif;font-weight:700;font-size:19px;color:var(--navy);padding-top:6px;line-height:22px}
.news-date span{font-size:9.6px}
.news-body{font-size:8.8px;line-height:15px;width:150px}
.news-body b{display:block;font-weight:700;color:var(--navy);font-size:8.8px}

.site-footer{position:absolute;top:1126px;left:0;width:720px;height:74px;background:var(--navy);color:var(--white)}
.footer-nav{position:absolute;left:47px;top:20px;display:flex;gap:24px;font-size:10.4px}
.copyright{position:absolute;left:47px;top:47px;font-size:9.6px}
.social{position:absolute;right:47px;top:18px;display:flex;gap:20px}
.social span{width:38px;height:38px;border-radius:50%;border:1.5px solid var(--white)}
.social span.active{background:var(--white)}
</style>
</head>
<body>

<header class="site-header">
  <div class="brand"><span class="brand-mark"></span><span class="brand-name">Tolvane, Inc.</span></div>
  <div class="hotline">
    <span class="hotline-label">FREE ADVICE</span>
    <svg width="15" height="15" viewBox="0 0 24 24"><path fill="#8b1a1a" d="M6.6 10.8a15.2 15.2 0 0 0 6.6 6.6l2.2-2.2c.3-.3.7-.4 1-.2 1.1.4 2.3.6 3.6.6.6 0 1 .4 1 1V20c0 .6-.4 1-1 1A17 17 0 0 1 3 4c0-.6.4-1 1-1h3.5c.6 0 1 .4 1 1 0 1.3.2 2.5.6 3.6.1.3 0 .7-.2 1z"/></svg>
    <span class="hotline-number">123 555 0142</span>
  </div>
  <nav class="main-nav">
    <span class="active">HOME</span><span>CONSUMER INFORMATION</span><span>CAREER</span><span>CONTACT</span>
  </nav>
</header>

<section class="hero">
  <div class="hero-photo" role="img" aria-label="Photo of a smiling support agent wearing a headset, with a blurred office colleague behind"></div>
  <h1 class="hero-title">ASSIST CONSUMERS IN<br>RESOLVING THEIR<br>OBLIGATIONS</h1>
  <div class="hero-button">EMPLOYMENT APPLICATION FORM</div>
</section>

<section class="welcome">
  <h2 class="section-title">WELCOME TO <em>TOLVANE INC.</em></h2>
  <p>Tolvane is a third party debt collection agency that is focused on the collection of higher education loans. Tolvane is compliant with all federal, state, and local laws and is committed to the professional and fair treatment of consumers. Our goal is to assist consumers in resolving their obligations in the manner that best meets their needs and to provide information necessary in order for consumers to make an informed decision.</p>
</section>

<section class="credentials">
  <div class="credential left">
    <div class="credential-badge"><span role="img" aria-label="Association membership badge"></span></div>
    <div class="credential-text">
      <h3>Member of Halvern<br>Credit Association</h3>
      <p>Lorem Ipsum is simply dummy text of the printing and typesetting industry. Lorem Ipsum has been the industry's standard dummy text ever since the 1500.</p>
    </div>
  </div>
  <div class="divider"></div>
  <div class="credential right">
    <div class="credential-badge round"><span role="img" aria-label="Accreditation badge"></span></div>
    <div class="credential-text">
      <h3>Accredited by the Trusted<br>Commerce Council</h3>
      <p>Lorem Ipsum is simply dummy text of the printing and typesetting industry. Lorem Ipsum has been the industry's standard dummy text ever since the 1500.</p>
    </div>
  </div>
</section>

<section class="testimonials">
  <h2 class="section-title">WHAT OUR <em>CLIENT SAY</em></h2>
  <svg class="quote-icon" width="20" height="16" viewBox="0 0 20 16"><path fill="#888" d="M0 16V9C0 4 2 1 7 0l1 2C5 3 4 5 4 7h4v9zm11 0V9c0-5 2-8 7-9l1 2c-3 1-4 3-4 5h4v9z"/></svg>
  <blockquote>Lorem Ipsum is simply dummy text of the printing and typesetting industry. Lorem Ipsum has been the industry's standard dummy text ever since the 1500s, when an unknown printer took a galley of type and scrambled it to make a type specimen book.</blockquote>
  <div class="client-name">- CLIENT NAME</div>
  <div class="slide-arrow prev"><svg width="10" height="20" viewBox="0 0 10 20"><path d="M8 1 2 10l6 9" fill="none" stroke="#262a6e" stroke-width="1.3"/></svg></div>
  <div class="slide-arrow next"><svg width="10" height="20" viewBox="0 0 10 20"><path d="M2 1l6 9-6 9" fill="none" stroke="#262a6e" stroke-width="1.3"/></svg></div>
</section>

<section class="news">
  <h2 class="section-title">LATEST <em>NEWS</em></h2>
  <div class="news-list">
    <article class="news-item" style="left:47px">
      <div class="news-date"><strong>21</strong><span>Apr</span></div>
      <div class="news-body">Lorem Ipsum is simply dummy text of the print &amp; typesetting industry.<b>READ MORE</b></div>
    </article>
    <article class="news-item" style="left:261px">
      <div class="news-date"><strong>20</strong><span>Apr</span></div>
      <div class="news-body">Lorem Ipsum is simply dummy text of the print &amp; typesetting industry.<b>READ MORE</b></div>
    </article>
    <article class="news-item" style="left:480px">
      <div class="news-date"><strong>19</strong><span>Apr</span></div>
      <div class="news-body">Lorem Ipsum is simply dummy text of the print &amp; typesetting industry.<b>READ MORE</b></div>
    </article>
  </div>
</section>

<footer class="site-footer">
  <nav class="footer-nav"><span>Home</span><span>Consumer</span><span>Career</span><span>Discloser</span></nav>
  <div class="copyright">© Tolvane Inc. - 2016. All Rights Reserved.</div>
  <div class="social">
    <span class="active" role="img" aria-label="Social profile link"></span>
    <span role="img" aria-label="Social profile link"></span>
    <span role="img" aria-label="Social profile link"></span>
  </div>
</footer>

</body>
</html>
```